Business Card Design

WE are looking for a premium quality Business Cards for a Law Firm . Copies of our current business card is attached.

Contact Information for Business Card

xyz

```html
<!DOCTYPE html>
<html lang="en">
<head>
<meta charset="utf-8">
<title>Harcourt Lawyers – Business Card</title>
<link href="https://fonts.googleapis.com/css2?family=Tinos:wght@400;700&display=swap" rel="stylesheet">
<style>
  :root{
    --stage:#ecebe8;
    --green:#0e2a1f;
    --green-light:#24463a;
    --gold:#c4a25d;
    --ink:#111111;
    --paper:#ffffff;
    --shade:#d9d9db;
  }
  *{box-sizing:border-box;margin:0;padding:0}
  html,body{width:1200px;height:780px;overflow:hidden;background:var(--stage)}
  .canvas{position:relative;width:1200px;height:780px;font-family:"Tinos",serif}
  .card{position:absolute;top:80px;width:330px;height:620px;box-shadow:0 10px 28px rgba(0,0,0,.22)}
  .card--back{left:220px;background:var(--green);overflow:hidden}
  .card--front{left:650px;background:var(--paper);overflow:hidden}

  .back-pattern{position:absolute;inset:0;background:
    radial-gradient(circle at 0% 10%, var(--green-light) 0%, rgba(36,70,58,.4) 35%, rgba(14,42,31,0) 65%),
    var(--green)}
  .back-brand{position:absolute;top:34px;right:28px;display:flex;align-items:center;gap:8px;color:var(--paper);font-weight:700;font-size:13px;letter-spacing:.12em}
  .brand-dot{width:22px;height:22px;border:1.5px solid currentColor;border-radius:50%}

  .front-art{position:absolute;inset:0}
  .front-brand{position:absolute;top:46px;left:0;right:0;display:flex;flex-direction:column;align-items:center;gap:12px;color:var(--green)}
  .front-brand .brand-dot{width:58px;height:58px;border:3px solid var(--gold)}
  .front-brand .brand-name{font-weight:700;font-size:22px;letter-spacing:.1em;text-align:center;line-height:1.15}

  .person{position:absolute;top:225px;left:0;right:0;text-align:center}
  .person-name{color:var(--gold);font-weight:700;font-size:31px;letter-spacing:.03em}
  .person-role{color:var(--ink);font-weight:700;font-size:14px;margin-top:4px;line-height:1.25}

  .icon-row{position:absolute;top:320px;left:0;right:0;display:flex;justify-content:center;gap:7px}
  .icon{width:24px;height:24px;border-radius:50%;background:var(--gold);display:flex;align-items:center;justify-content:center}
  .icon svg{width:13px;height:13px}

  .contact{position:absolute;top:356px;left:0;right:0;text-align:center;color:var(--ink);font-weight:700;font-size:14.5px;line-height:1.35}

  .address{position:absolute;top:520px;left:0;right:0;text-align:center;color:var(--ink);font-weight:700;font-size:14px;line-height:1.3}
  .address .icon{margin:0 auto 8px}
</style>
</head>
<body>
<main class="canvas">

  <section class="card card--back">
    <div class="back-pattern" role="img" aria-label="Repeating monogram pattern fading from light to dark green"></div>
    <div class="back-brand"><span class="brand-dot"></span><span>HARCOURT LAWYERS</span></div>
  </section>

  <section class="card card--front">
    <svg class="front-art" viewBox="0 0 330 620" width="330" height="620" aria-hidden="true">
      <defs>
        <linearGradient id="swoop-grey" x1="0" y1="0" x2="0" y2="1">
          <stop offset="0" stop-color="#c9c9cc"/>
          <stop offset=".5" stop-color="#eeeeef"/>
          <stop offset="1" stop-color="#ffffff"/>
        </linearGradient>
        <linearGradient id="swoop-light" x1="0" y1="0" x2="1" y2="1">
          <stop offset="0" stop-color="#ffffff"/>
          <stop offset="1" stop-color="#f1f1f2"/>
        </linearGradient>
      </defs>
      <path d="M0,430 Q150,520 330,300 L330,620 L0,620Z" fill="url(#swoop-grey)"/>
      <path d="M0,470 Q170,505 330,395 L330,620 L0,620Z" fill="url(#swoop-light)"/>
      <path d="M0,620 L0,585 Q140,470 330,440 L330,620Z" fill="#ffffff"/>
    </svg>

    <header class="front-brand">
      <span class="brand-dot"></span>
      <span class="brand-name">HARCOURT<br>LAWYERS</span>
    </header>

    <div class="person">
      <h1 class="person-name">DANIEL REYES</h1>
      <p class="person-role">Director and Principal Solicitor<br>MBA, Juris Doctor</p>
    </div>

    <div class="icon-row">
      <span class="icon"><svg viewBox="0 0 24 24"><path fill="#fff" d="M6.6 10.8a15 15 0 0 0 6.6 6.6l2.2-2.2c.3-.3.7-.4 1-.2 1.1.4 2.3.6 3.6.6.6 0 1 .4 1 1V20c0 .6-.4 1-1 1A17 17 0 0 1 3 4c0-.6.4-1 1-1h3.5c.6 0 1 .4 1 1 0 1.3.2 2.5.6 3.6.1.3 0 .7-.2 1z"/></svg></span>
      <span class="icon"><svg viewBox="0 0 24 24"><rect x="6" y="2" width="12" height="20" rx="2" fill="none" stroke="#fff" stroke-width="2"/><circle cx="12" cy="18" r="1.2" fill="#fff"/></svg></span>
      <span class="icon"><svg viewBox="0 0 24 24"><rect x="3" y="5" width="18" height="14" rx="1.5" fill="none" stroke="#fff" stroke-width="2"/><path d="M3 6l9 7 9-7" fill="none" stroke="#fff" stroke-width="2"/></svg></span>
      <span class="icon"><svg viewBox="0 0 24 24"><circle cx="12" cy="12" r="9" fill="none" stroke="#fff" stroke-width="2"/><path d="M3 12h18M12 3c3 3 3 15 0 18M12 3c-3 3-3 15 0 18" fill="none" stroke="#fff" stroke-width="1.6"/></svg></span>
    </div>

    <address class="contact">
      +61 7 3555 0142<br>
      +61 0400 555 318<br>
      www.harcourtlawyers.com.au<br>
      daniel@harcourtlawyers.com.au
    </address>

    <address class="address">
      <span class="icon"><svg viewBox="0 0 24 24"><path fill="#fff" d="M12 2a7 7 0 0 0-7 7c0 5 7 13 7 13s7-8 7-13a7 7 0 0 0-7-7zm0 9.5A2.5 2.5 0 1 1 12 6.5a2.5 2.5 0 0 1 0 5z"/></svg></span>
      Level 3, Harcourt House,<br>
      210 Ashby Terrace,<br>
      Kelvin Grove, QLD 4059
    </address>
  </section>

</main>
</body>
</html>
```